BildeVOLD buisnesscard

Hey :) I need a modern buisnesscard for my company BildeVOLD
It most have:
Dagligleder og Fotograf: Henrik Audun Strandvik

Mob: +4791264085
Epost: post@bildevold.example
Adresse: Kvernbakken9, 6040 Fjordvik

Facbook and instagram logo with text BildeVOLD

BildeVOLD logo

It Company

```html
<!DOCTYPE html>
<html lang="no">
<head>
<meta charset="utf-8">
<title>BildeVOLD – visittkort</title>
<link href="https://fonts.googleapis.com/css2?family=Montserrat:wght@400;500;600;700&display=swap" rel="stylesheet">
<style>
  :root {
    --stage: #2b2b2b;
    --card: #050505;
    --silver: #c9c9c9;
    --silver-light: #ececec;
    --text-light: #e6e6e6;
    --text-muted: #a8a8a8;
  }
  * { margin: 0; padding: 0; box-sizing: border-box; }
  html, body {
    width: 1200px; height: 900px; overflow: hidden;
    background: var(--stage);
    font-family: "Montserrat", sans-serif;
  }
  .canvas { position: relative; width: 1200px; height: 900px; }

  .card {
    position: absolute;
    width: 665px; height: 380px;
    background: var(--card);
    border-radius: 22px;
    overflow: hidden;
    box-shadow: 0 18px 40px rgba(0,0,0,.55);
  }
  .card--front { left: 60px; top: 50px; }
  .card--back { left: 475px; top: 470px; }

  .card__edge { position: absolute; left: 0; bottom: 0; width: 100%; height: 40px; }

  /* front */
  .front__brand {
    position: absolute; inset: 0 0 40px 0;
    display: flex; align-items: center; justify-content: center;
  }
  .brand-name {
    color: var(--silver);
    font-weight: 700;
    font-size: 64px;
    letter-spacing: -1px;
    white-space: nowrap;
  }

  /* back */
  .back__brand {
    position: absolute; left: 30px; top: 150px; width: 260px;
    display: flex; justify-content: center;
  }
  .back__brand .brand-name { font-size: 40px; }
  .back__divider {
    position: absolute; left: 305px; top: 110px;
    width: 1px; height: 150px;
    background: linear-gradient(to bottom, transparent, var(--silver), transparent);
  }
  .person { position: absolute; left: 330px; top: 112px; }
  .person__name { color: var(--text-light); font-weight: 600; font-size: 22px; white-space: nowrap; }
  .person__title { color: var(--text-muted); font-size: 14px; margin-top: 4px; }
  .contact { list-style: none; margin-top: 18px; }
  .contact li {
    display: flex; align-items: center; gap: 9px;
    color: var(--text-light); font-size: 15px; margin-bottom: 6px;
    white-space: nowrap;
  }
  .contact svg { width: 12px; height: 12px; fill: var(--text-light); flex: none; }
  .social {
    position: absolute; right: 38px; top: 282px;
    display: flex; align-items: center; gap: 7px;
    color: var(--text-light); font-size: 14px;
  }
  .social__dot { width: 10px; height: 10px; border-radius: 50%; background: var(--text-light); }
</style>
</head>
<body>
<main class="canvas">

  <section class="card card--front" aria-label="Visittkort forside">
    <div class="front__brand"><span class="brand-name">BildeVOLD</span></div>
    <svg class="card__edge" viewBox="0 0 665 40" preserveAspectRatio="none" aria-hidden="true">
      <rect x="0" y="26" width="665" height="14" fill="var(--silver)"/>
      <path d="M0 26 H420 Q432 26 440 14 H665 V26 H0 Z" fill="var(--silver-light)"/>
      <path d="M0 0 H665 V14 H440 Q432 14 420 24 H0 Z" fill="var(--card)"/>
    </svg>
  </section>

  <section class="card card--back" aria-label="Visittkort bakside">
    <div class="back__brand"><span class="brand-name">BildeVOLD</span></div>
    <div class="back__divider"></div>
    <div class="person">
      <p class="person__name">Henrik Audun Strandvik</p>
      <p class="person__title">Dagligleder og Fotograf</p>
      <ul class="contact">
        <li>
          <svg viewBox="0 0 24 24"><path d="M6.6 10.8a15 15 0 0 0 6.6 6.6l2.2-2.2a1 1 0 0 1 1-.25 11.4 11.4 0 0 0 3.6.57 1 1 0 0 1 1 1V20a1 1 0 0 1-1 1A17 17 0 0 1 3 4a1 1 0 0 1 1-1h3.5a1 1 0 0 1 1 1c0 1.25.2 2.45.57 3.57a1 1 0 0 1-.25 1z"/></svg>
          +4791264085
        </li>
        <li>
          <svg viewBox="0 0 24 24"><path d="M2 5h20v14H2z M4 7v.5l8 5 8-5V7l-8 5z" fill-rule="evenodd"/></svg>
          post@bildevold.example
        </li>
        <li>
          <svg viewBox="0 0 24 24"><path d="M12 2a7 7 0 0 0-7 7c0 5.25 7 13 7 13s7-7.75 7-13a7 7 0 0 0-7-7zm0 9.5A2.5 2.5 0 1 1 12 6.5a2.5 2.5 0 0 1 0 5z"/></svg>
          Kvernbakken9, 6040 Fjordvik
        </li>
      </ul>
    </div>
    <div class="social"><span class="social__dot"></span><span>BildeVOLD</span></div>
    <svg class="card__edge" viewBox="0 0 665 40" preserveAspectRatio="none" aria-hidden="true">
      <rect x="0" y="26" width="665" height="14" fill="var(--silver)"/>
      <path d="M0 26 H420 Q432 26 440 14 H665 V26 H0 Z" fill="var(--silver-light)"/>
      <path d="M0 0 H665 V14 H440 Q432 14 420 24 H0 Z" fill="var(--card)"/>
    </svg>
  </section>

</main>
</body>
</html>
```